Modern Business Card for Larkwell 2018

Our company assumes the best about people. We are creating an online community of entrepreneurs and business leaders who struggle with marketing their business online.

This business card should POP! We recently got a new logo and are launching a new website next month, so our business cards should make a statement that feels:
-Fresh
-Smart
-Trustworthy
-Fun

Target Market(s)

small business owners, entrepreneurs

Industry/Entity Type

Digital Marketing

Contact Information for Business Card

Dimensions: 3.5" x 2"

Font styles to use
Sans Serif

Colors
f37122
ffffff

Requirements
Must have
• We need a business card with a modern, bold design. We will use one side of the card as a lead-generation offer, so text on one side will need to fit up to 140 characters. The business card should stick to our core colors (orange, black, and white).
Nice to have
• We think a vertical "portrait" design could be interesting.
Should not have
• Should not look like a traditional business card. The round icon should stand out from a distance.

```html
<!DOCTYPE html>
<html lang="en">
<head>
<meta charset="utf-8">
<title>Larkwell Business Card</title>
<link href="https://fonts.googleapis.com/css2?family=Open+Sans:wght@400;700;800&family=Great+Vibes&display=swap" rel="stylesheet">
<style>
  :root {
    --orange: #f37122;
    --orange-deep: #e8631a;
    --white: #ffffff;
    --paper: #f4f4f4;
    --ink: #151515;
    --grey: #555555;
    --backdrop: #2e2f31;
    --field: #e6e6e6;
  }
  * { box-sizing: border-box; margin: 0; padding: 0; }
  html, body { width: 1200px; height: 960px; overflow: hidden; }
  body {
    background: var(--backdrop);
    font-family: "Open Sans", Arial, sans-serif;
    display: flex;
    flex-direction: column;
    align-items: center;
    justify-content: center;
    gap: 60px;
  }
  .card {
    width: 700px;
    height: 400px;
    position: relative;
    overflow: hidden;
  }

  /* Back: lead-generation side */
  .card-back { background: var(--orange); color: var(--white); }
  .brand {
    position: absolute;
    left: 40px; top: 70px;
    width: 300px;
    text-align: center;
  }
  .brand-dot {
    width: 44px; height: 44px;
    border-radius: 50%;
    background: var(--white);
    margin: 0 auto 12px;
  }
  .brand-name {
    font-weight: 800;
    font-size: 50px;
    letter-spacing: 2px;
    line-height: 1;
  }
  .brand-tagline {
    font-weight: 700;
    font-size: 13px;
    letter-spacing: 2.4px;
    margin-top: 6px;
    text-transform: uppercase;
  }
  .divider {
    position: absolute;
    left: 372px; top: 40px;
    width: 1px; height: 190px;
    background: rgba(255,255,255,0.6);
  }
  .offer {
    position: absolute;
    left: 398px; top: 40px;
    width: 280px;
  }
  .offer-headline {
    font-weight: 800;
    font-size: 21px;
    line-height: 1.02;
    text-transform: uppercase;
  }
  .offer-body {
    font-size: 15px;
    line-height: 1.25;
    margin-top: 10px;
  }
  .offer-url {
    font-weight: 700;
    font-size: 17px;
    margin-top: 14px;
  }
  .note-field {
    position: absolute;
    left: 40px; right: 24px;
    top: 262px; height: 100px;
    background: var(--field);
    border-radius: 24px;
  }
  .note-field .rule {
    position: absolute;
    left: 60px; right: 40px;
    height: 1px;
    background: var(--ink);
  }
  .note-field .rule-1 { top: 34px; }
  .note-field .rule-2 { top: 68px; }

  /* Front: personal side */
  .card-front {
    background: var(--paper);
    border: 16px solid var(--orange);
  }
  .front-dot {
    position: absolute;
    left: 340px; top: 62px;
    width: 80px; height: 80px;
    border-radius: 50%;
    background: var(--orange-deep);
  }
  .person {
    position: absolute;
    left: 120px; top: 150px;
    width: 500px;
  }
  .person-name {
    font-family: "Great Vibes", cursive;
    color: var(--orange-deep);
    font-size: 76px;
    line-height: 1;
    white-space: nowrap;
  }
  .person-title {
    font-weight: 800;
    font-size: 26px;
    color: var(--ink);
    text-transform: uppercase;
    margin-top: -6px;
    padding-left: 20px;
  }
  .person-email {
    font-size: 20px;
    color: var(--grey);
    padding-left: 56px;
    margin-top: 2px;
  }
</style>
</head>
<body>
  <section class="card card-back">
    <div class="brand">
      <div class="brand-dot"></div>
      <div class="brand-name">LARKWELL</div>
      <div class="brand-tagline">Tell stories that inspire action</div>
    </div>
    <div class="divider"></div>
    <div class="offer">
      <p class="offer-headline">Reach more people.<br>Make more money.<br>Create more impact.</p>
      <p class="offer-body">Get your free Larkwell Starter Package and our marketing guide today at</p>
      <p class="offer-url">Larkwellnow.com/start</p>
    </div>
    <div class="note-field">
      <span class="rule rule-1"></span>
      <span class="rule rule-2"></span>
    </div>
  </section>

  <section class="card card-front">
    <div class="front-dot"></div>
    <div class="person">
      <p class="person-name">Dana Whitlow</p>
      <p class="person-title">Story Marketing Coach</p>
      <p class="person-email">dana@larkwellnow.com</p>
    </div>
  </section>
</body>
</html>
```